Lotus Ridge Website

We need a website that has clean, asian looking images that relax and motivate people to come into our integrated medical center. My current website is www.needlecalmharbor.com and I would like the design for Lotus Ridge Wellness Partners to be similar but more inviting with video content and a product purchase store as well. A moving banner would be nice too. When people are looking for ways of losing weight or getting out of pain we want them to make the connection that we have the solution. This website needs to provide sufficient information so that patients are well informed and choose us as their health provider before they ever walk through our doors. We offer comprehensive natural medicine that is based on the principles that the body can heal itself when given the right conditions. Our services include medical weight loss and hormone balancing, acupuncture and chinese herbal medicine, physical medicine, trigger point injections, allergy testing and joint rehabilitation. The Medical Doctor and Licensed Acupuncturist work as a team to provide optimal care that is catered to each individual who comes through our doors.
Updates

Target Market(s)

40 to 50 year olds who want to lose weight or have pain issues.

Industry/Entity Type

Medical

Requirements
Must have
• Use photos from our website www.needlecalmharbor.com or similar content. Video content. Moving banner with relaxing images.
Nice to have
• Happy, healthy looking people. Medical Doctors working as a team. Friendly staff in a cutting edge facility.
Should not have
• Papyrus font, or big bold words.

```html
<!DOCTYPE html>
<html lang="en">
<head>
<meta charset="utf-8">
<title>Lotus Ridge Website</title>
<link href="https://fonts.googleapis.com/css2?family=Cabin+Condensed:wght@500&family=Open+Sans:wght@400&display=swap" rel="stylesheet">
<style>
:root{
  --olive:#6b6a2b;
  --olive-dark:#57561f;
  --tab-top:#e6e79a;
  --tab-bottom:#b8ba4c;
  --ink:#111;
  --navy:#1e2838;
  --band:#f3f1ec;
  --footer:#e8e38a;
  --rule:#b7b37a;
}
*{margin:0;padding:0;box-sizing:border-box}
html,body{width:961px;height:1200px;overflow:hidden;background:#fff}
body{position:relative;font-family:Arial,Helvetica,sans-serif;color:var(--ink)}
.abs{position:absolute}
.top-stripe{left:0;top:0;width:961px;height:6px;border-top:2px solid #2c2c1c;border-bottom:2px solid var(--olive)}
.brand{left:113px;top:6px;width:99px;height:134px;background:var(--olive);box-shadow:1px 2px 4px rgba(0,0,0,.35);display:flex;align-items:center;justify-content:center}
.brand span{color:#fff;font-family:'Open Sans',sans-serif;font-size:13px;letter-spacing:1px;text-align:center;line-height:18px}
.social{top:37px;display:flex;gap:6px;left:772px}
.social i{display:block;width:16px;height:16px;background:#222;border-radius:2px}
.nav{top:97px;left:0}
.tab{position:absolute;top:0;height:33px;width:75px;background:linear-gradient(var(--tab-top),var(--tab-bottom));border-radius:3px 3px 0 0;font-family:'Open Sans',sans-serif;font-size:11.5px;color:#1b1b10;text-align:center;line-height:36px;white-space:nowrap}
.tab.active{top:-1px;height:34px;background:linear-gradient(#cfd06a,#a9ab3c)}
.hero{left:101px;top:130px;width:762px;height:245px;border:1px solid var(--olive);background:#fbfaf8;overflow:hidden}
.hero .pose-a{position:absolute;left:184px;top:10px;width:335px;height:232px;background:radial-gradient(ellipse at 60% 55%,#e9d2bf,#f4ebe3 55%,#fbfaf8 75%)}
.hero .pose-b{position:absolute;left:538px;top:5px;width:172px;height:225px;background:radial-gradient(ellipse at 50% 45%,#dcb69a,#efdccd 50%,#fbfaf8 72%)}
.headline{font-family:'Cabin Condensed',sans-serif;font-size:25px;color:var(--navy)}
.dropdown{left:459px;top:130px;width:140px;height:171px;background:rgba(196,196,140,.72);padding:8px 0 0 18px}
.dropdown li{list-style:none;font-size:10px;line-height:19.3px;color:#1a1a1a;white-space:nowrap}
.video-box{left:101px;top:380px;width:224px;height:230px;border:1px solid var(--olive);border-radius:4px 4px 0 0;background:linear-gradient(#6b6a2b 0,#d8d7b8 30px,#fff 45px)}
.video-box .icon{position:absolute;left:7px;top:8px;width:43px;height:32px;background:#333;border:2px solid #ddd}
.video-box h2{position:absolute;left:56px;top:10px;font-family:'Open Sans',sans-serif;font-weight:400;font-size:21px;color:#111}
.player{left:9px;top:51px;width:206px;height:155px;background:#000}
.player .hint{position:absolute;left:10px;bottom:10px;font-size:4.5px;color:#bbb;letter-spacing:.5px}
.controls{left:9px;top:206px;width:206px;height:14px;background:#eee;border:1px solid #ccc}
.section-title{font-family:'Open Sans',sans-serif;font-weight:400;color:var(--olive-dark);white-space:nowrap}
.read-more{font-size:8px;color:#222}
.body-copy{font-size:10.8px;line-height:19.3px;color:#111;white-space:nowrap}
.products{left:0;top:626px;width:961px;height:164px;background:linear-gradient(#fdfcfb,var(--band));border-top:1px solid var(--rule);border-bottom:1px solid var(--rule)}
.product{position:absolute;top:35px;width:95px;text-align:center}
.product .thumb{width:95px;height:95px;border:1px solid #aaa;background:#fff;display:flex;align-items:center;justify-content:center;font-family:Georgia,serif;font-size:12px;color:#888;line-height:14px}
.product p{font-size:10px;margin-top:8px}
.col{position:absolute;top:808px}
.col h3{font-size:14px;border-bottom:1px solid var(--rule);padding-bottom:5px;margin-bottom:7px}
.footer{left:0;top:971px;width:961px;height:197px;background:var(--footer)}
.footer ul{position:absolute;top:13px;list-style:none}
.footer li{font-size:8px;line-height:19.2px;color:#111;white-space:nowrap}
.map{left:569px;top:18px;width:285px;height:135px;background:linear-gradient(135deg,#d9d6cf,#c9c6bd 50%,#dedbd3)}
.copyright{left:0;top:1178px;width:961px;text-align:center;font-size:8px}
</style>
</head>
<body>
<div class="abs top-stripe"></div>
<div class="abs brand"><span>LOTUS<br>RIDGE</span></div>
<div class="abs social" aria-label="Social links"><i></i><i></i><i></i></div>

<nav class="abs nav">
  <div class="tab" style="left:226px">Sai Toi Ha</div>
  <div class="tab" style="left:304px">Seitai Shinpo</div>
  <div class="tab" style="left:382px">Acupuncture</div>
  <div class="tab active" style="left:460px">Services</div>
  <div class="tab" style="left:538px">Biography</div>
  <div class="tab" style="left:617px">Nutrition</div>
  <div class="tab" style="left:695px">My Journey</div>
  <div class="tab" style="left:773px">Contact Us</div>
</nav>

<section class="abs hero">
  <div class="pose-a" role="img" aria-label="Photo of a woman in a relaxing stretching pose"></div>
  <div class="pose-b" role="img" aria-label="Photo of a woman seen from behind, stretching her shoulder"></div>
  <div class="abs headline" style="left:38px;top:32px">Main Head Line</div>
  <div class="abs headline" style="left:91px;top:76px">Punch Line</div>
</section>
<ul class="abs dropdown">
  <li>medical weight loss</li><li>hormone balancing</li><li>acupuncture</li><li>chinese herbal medicine</li><li>physical medicine</li><li>&nbsp;trigger point injections</li><li>&nbsp;allergy testing</li><li>&nbsp;joint rehabilitation</li>
</ul>

<section class="abs video-box">
  <div class="icon"></div>
  <h2>Our Video</h2>
  <div class="abs player">
    <svg class="abs" style="left:98px;top:72px" width="10" height="11"><polygon points="0,0 10,5.5 0,11" fill="#fff"/></svg>
    <div class="hint">PRESS PLAY TO WATCH</div>
  </div>
  <div class="abs controls">
    <svg width="204" height="12"><polygon points="5,2 12,6 5,10" fill="#333"/><rect x="50" y="5" width="72" height="3" rx="1.5" fill="#999"/><circle cx="53" cy="6.5" r="3" fill="#333"/></svg>
  </div>
</section>

<h2 class="abs section-title" style="left:339px;top:391px;font-size:20px">Welcome to Lotus Ridge Acupuncture</h2>
<div class="abs read-more" style="left:810px;top:404px">read more&gt;&gt;</div>
<div class="abs" style="left:335px;top:421px;width:527px;border-top:1px solid var(--rule)"></div>
<div class="abs body-copy" style="left:340px;top:429px;width:522px">
  <p>As the needles are carefully inserted into acupuncture points, specific cells stimulate nerve pathways that trigger<br>a healing response to a particular organ system or area of the body.&nbsp; Acupuncture also acts on the autonomic<br>nervous system and causes the release of endorphins, enkephalins and other natural pain relieving chemicals.</p>
  <p style="margin-top:19px">At Lotus Ridge Acupuncture the system of acupuncture used is called Seitai Shinpo (which translates into “correct<br>posture acupuncture method”) that uses acupuncture and moxibustion to balance structural distortions by<br>releasing tense areas of contraction along the spine.&nbsp; When the structure is properly balanced then the body will<br>heal much quicker.</p>
</div>

<section class="abs products">
  <h2 class="abs" style="left:104px;top:8px;font-family:'Open Sans',sans-serif;font-weight:400;font-size:14px">Our Featured Products</h2>
  <div class="product" style="left:131px"><div class="thumb">No Image<br>Available</div><p>Product one</p></div>
  <div class="product" style="left:252px"><div class="thumb">No Image<br>Available</div><p>Product two</p></div>
  <div class="product" style="left:372px"><div class="thumb">No Image<br>Available</div><p>Product three</p></div>
  <div class="product" style="left:493px"><div class="thumb">No Image<br>Available</div><p>Product four</p></div>
  <div class="product" style="left:613px"><div class="thumb">No Image<br>Available</div><p>Product five</p></div>
  <div class="product" style="left:743px"><div class="thumb">No Image<br>Available</div><p>Product six</p></div>
</section>

<div class="col" style="left:102px;width:235px">
  <h3 class="section-title">How does acupuncture work?</h3>
  <p class="body-copy" style="padding-left:4px">As the needles are carefully inserted into acupun<br>cture points, specific cells stimulate nerve path<br>ways that trigger a healing response to a particula<br>organ system or area of the body.&nbsp; Acupuncture<br>also acts on the autonomic nervous system and</p>
  <div class="read-more" style="padding-left:4px">read more&gt;&gt;</div>
</div>
<div class="col" style="left:344px;width:260px">
  <h3 class="section-title">What can be treated with acupuncture?</h3>
  <p class="body-copy" style="padding-left:4px">Acupuncture has been used to effectively treat numer<br>ous health conditions for thousands of years.&nbsp; Accordi<br>the Global Wellness Council, ¼ of the earth’s<br>population receives acupuncture treatment on a<br>continual basis.</p>
  <div class="read-more" style="padding-left:4px">read more&gt;&gt;</div>
</div>
<div class="col" style="left:609px;width:254px">
  <h3 class="section-title">How safe is acupuncture</h3>
  <p class="body-copy" style="padding-left:4px">Acupuncture needles are engineered so precisely that<br>usually a very mild sensation is felt, if any at all.&nbsp; The<br>needles are about the diameter of a hair.&nbsp; Most patient<br>report feeling deeply relaxed and often have instant<br>pain relief.</p>
  <div class="read-more" style="padding-left:4px;margin-top:3px">read more&gt;&gt;</div>
</div>

<footer class="abs footer">
  <ul style="left:108px"><li>home</li><li>So tai ho</li><li>Seitai Shinpo</li><li>Acupuncture</li><li>Biography</li><li>Nutrition</li><li>My Journey</li><li>Services</li><li>Contact Us</li></ul>
  <ul style="left:237px"><li>medical weight loss</li><li>hormone balancing</li><li>&nbsp;acupuncture</li><li>&nbsp;chinese herbal medicine</li><li>&nbsp;physical medicine</li><li>&nbsp;trigger point injections</li><li>&nbsp;allergy testing</li><li>&nbsp;&nbsp;joint rehabilitation</li></ul>
  <ul style="left:390px"><li>petalnet</li><li>chirpline</li><li>workcircle</li></ul>
  <div class="abs map" role="img" aria-label="Street map showing the clinic location"></div>
</footer>
<div class="abs copyright">Copyright 2007© Lotus Ridge Acupuncture — All Rights Reserved</div>
</body>
</html>
```